Professional Baby Bottle Bank Print Design

We need a baby bottle design that is 4.25" wide x 2.28" tall with a maximum of 6 colors (white is counted as a color).

The bottle design needs to be fun but professional. Bottles with cartoon images on it will be rejected immediately.

The bottle design wraps around the bottle. See examples here: https://vel.quin/cat/BabyBottles/HarlowBottles/5

Minimum font size is 10pt.

The bottle design must have the following text on it:
Main Text: Love them both
Paragraph text: Our ministry’s aim is to not only save unborn babies, but to provide love, support, and life-saving resources for vulnerable women in our community. By filling this bottle with cash, checks, and spare coins and returning it on collection day, you are truly saving and changing lives!
Optional text: Thank you!

We are including an example file and a template file. You do NOT have to use the template - but your file has to be the exact size mentioned. If you don't design as well as our sample, please don't waste our time by spamming us with hundreds of designs. We will ban design houses that spam us with designs that are more layouts (and not well designed).

Please note - white is a color. You don't have to do a box - but anything you don't make white will be see-through.

We will take the winners of this contest to a survey with the customers. We may choose two and edit the text of one slightly to be different. We must know the fonts used.

No gradients unless they are half-toned with relatively big sized dots.

Target Market(s)

Church Attendees coming from a Pregnancy Center

Industry/Entity Type

Religious Christian Churches

Requirements
Must have
• Professional, great palette, wording as described.
Nice to have
• Integrated design across the whole space with areas for text (no text all the way across)
Should not have
• Cartoon figures; elements shoved together that don't go together (i.e. - actually design something)

```html
<!DOCTYPE html>
<html lang="en">
<head>
<meta charset="utf-8">
<title>Love Them Both – Baby Bottle Label</title>
<link rel="stylesheet" href="https://fonts.googleapis.com/css2?family=Abril+Fatface&family=Baloo+2:wght@800&family=Source+Sans+3:wght@400&display=swap">
<style>
  :root {
    --stage: #39393b;
    --rose: #e87880;
    --rose-deep: #e4707b;
    --rose-light: #f39a9a;
    --cloud: #f6fbfd;
    --teal: #12869e;
    --white: #ffffff;
    --skin: #f49393;
    --sky: #c6e7f2;
  }
  * { margin: 0; padding: 0; box-sizing: border-box; }
  html, body {
    width: 1200px; height: 1000px; overflow: hidden;
    background: var(--stage);
  }
  .label {
    position: absolute;
    left: 143px; top: 253px;
    width: 913px; height: 490px;
    background: var(--rose);
    overflow: hidden;
  }
  .label__shapes { position: absolute; inset: 0; }
  .label__doodles {
    position: absolute;
    left: 640px; top: 20px;
    width: 250px; height: 220px;
    background: var(--rose-deep);
    border-radius: 40px;
    opacity: .6;
  }
  .label__illustration {
    position: absolute;
    left: 57px; top: 30px;
    width: 302px; height: 429px;
    border-radius: 150px 150px 120px 60px;
    background: linear-gradient(160deg, var(--skin) 0%, var(--sky) 55%, var(--skin) 100%);
  }
  .label__title {
    position: absolute;
    left: 385px; top: 46px;
    font-family: "Abril Fatface", serif;
    font-size: 90px;
    line-height: 71px;
    color: var(--white);
    letter-spacing: -1px;
  }
  .label__badge {
    position: absolute;
    left: 714px; top: 225px;
    width: 106px; height: 106px;
    border-radius: 50%;
    background: var(--teal);
    border: 3px dotted var(--teal);
    outline: 2px dotted var(--teal);
    outline-offset: 1px;
    display: flex; align-items: center; justify-content: center;
    text-align: center;
    font-family: "Baloo 2", sans-serif;
    font-weight: 800;
    font-size: 27px;
    line-height: 24px;
    color: var(--white);
  }
  .label__message {
    position: absolute;
    left: 339px; top: 340px;
    width: 540px;
    font-family: "Source Sans 3", sans-serif;
    font-size: 18.5px;
    line-height: 25.2px;
    color: var(--teal);
  }
</style>
</head>
<body>
  <section class="label">
    <svg class="label__shapes" width="913" height="490" viewBox="0 0 913 490" aria-hidden="true">
      <ellipse cx="120" cy="70" rx="90" ry="60" fill="var(--rose-deep)" opacity=".5"/>
      <ellipse cx="300" cy="40" rx="80" ry="50" fill="var(--rose-deep)" opacity=".5"/>
      <path class="title-blob" d="M480 30 C560 15 620 60 630 150 C640 230 580 290 470 292 C400 294 365 270 362 205 C360 150 390 110 420 80 C440 55 455 35 480 30 Z" fill="var(--rose-light)"/>
      <path class="cloud" fill="var(--cloud)" d="M0 285 C30 270 70 270 100 282 L300 330 C320 305 345 300 385 318 C420 300 460 302 500 318 C530 290 565 290 593 303 C640 270 680 290 720 300 C770 250 820 236 860 236 C885 236 900 236 913 236 L913 490 L0 490 Z"/>
    </svg>
    <div class="label__doodles" role="img" aria-label="Decorative line doodles of a heart, a cross and floating bubbles"></div>
    <div class="label__illustration" role="img" aria-label="Illustration of a mother tenderly cradling her swaddled newborn baby"></div>
    <h1 class="label__title">Love<br>Them<br>Both</h1>
    <div class="label__badge">Thank<br>You!</div>
    <p class="label__message">Our ministry’s aim is to not only save unborn babies,<br>but to provide love, support, and life-saving resources for<br>vulnerable women in our community. By filling this bottle<br>with cash, checks, and spare coins and returning it on<br>collection day, you are truly saving and changing lives!</p>
  </section>
</body>
</html>
```